Business card design

I already have the logo design completed and am requiring business card design and layout utilising the logo. I require a front and back design.

We are an executive recruitment company so we are looking at full colour, high finish in a reasonably conservative structure.

Reason: will be provide ai template

Target Market(s)

Senior Management 35-60 age bracket

Industry/Entity Type

Business

Requirements
Must have
• Peter Welling
• Director
• 238 Morrow Tce, Kelvin Grove QLD 4059
• Ph: 07 3628 4190 Mob: 0418527306
• peter@voltinapartners.com.au
• www.voltinapartners.com.au
Nice to have
• Ideally full colour,
Should not have
• cheap looking

```html
<!DOCTYPE html>
<html lang="en">
<head>
<meta charset="utf-8">
<title>Voltina Partners – Business Card</title>
<link rel="stylesheet" href="https://fonts.googleapis.com/css2?family=Open+Sans:wght@400;600;700&display=swap">
<style>
  :root {
    --backdrop: #d2d2d2;
    --paper: #ffffff;
    --navy: #1d3f6e;
    --navy-deep: #0c3263;
    --navy-light: #174676;
    --stripe: #0b3a6f;
    --grey-text: #8e8e8e;
    --grey-title: #6a6a6a;
    --white: #ffffff;
  }
  * { box-sizing: border-box; margin: 0; padding: 0; }
  html, body {
    width: 1105px;
    height: 1200px;
    overflow: hidden;
    background: var(--backdrop);
    font-family: "Open Sans", Arial, sans-serif;
  }
  .canvas {
    position: relative;
    width: 1105px;
    height: 1200px;
  }
  .card {
    position: absolute;
    top: 477px;
    width: 443px;
    height: 246px;
    overflow: hidden;
  }
  /* Front */
  .card--front {
    left: 78px;
    background: var(--paper);
  }
  .card--front .edge-stripe {
    position: absolute;
    right: 0; top: 0;
    width: 9px; height: 100%;
    background: var(--stripe);
  }
  .brand {
    position: absolute;
    display: flex;
    align-items: center;
    gap: 8px;
    font-weight: 700;
    letter-spacing: 0.06em;
    text-transform: uppercase;
    white-space: nowrap;
  }
  .brand__mark {
    display: block;
    width: 22px; height: 22px;
  }
  .card--front .brand {
    left: 36px; top: 42px;
    font-size: 19px;
    color: var(--navy);
  }
  .card--front .brand__mark { background: var(--navy); }
  .holder {
    position: absolute;
    left: 35px; top: 131px;
  }
  .holder__name {
    font-size: 18px;
    font-weight: 700;
    color: var(--navy);
    line-height: 1.2;
  }
  .holder__title {
    font-size: 14px;
    color: var(--grey-title);
    line-height: 1.2;
  }
  .contact {
    position: absolute;
    right: 22px; top: 128px;
    list-style: none;
    font-size: 11px;
    line-height: 19px;
    color: var(--grey-text);
    letter-spacing: 0.03em;
    white-space: nowrap;
  }
  /* Back */
  .card--back {
    left: 591px;
    background: linear-gradient(160deg, var(--navy-light) 0%, var(--navy-deep) 55%, #0a2c59 100%);
  }
  .card--back .edge-shade {
    position: absolute;
    right: 0; top: 0;
    width: 9px; height: 100%;
    background: linear-gradient(180deg, #9a9a9a, #3a3a3a);
  }
  .card--back .brand {
    left: calc(50% - 4px); top: 106px;
    transform: translateX(-50%);
    font-size: 21px;
    color: var(--white);
  }
  .card--back .brand__mark { background: var(--white); }
  .website {
    position: absolute;
    left: 0; right: 9px;
    top: 216px;
    text-align: center;
    font-size: 15px;
    font-weight: 600;
    letter-spacing: 0.05em;
    color: var(--white);
  }
</style>
</head>
<body>
<main class="canvas">
  <section class="card card--front" aria-label="Business card front">
    <div class="brand"><span class="brand__mark"></span>Voltina Partners</div>
    <div class="holder">
      <p class="holder__name">Peter Welling</p>
      <p class="holder__title">Director</p>
    </div>
    <ul class="contact">
      <li>xxxx xxxx xxxx</li>
      <li>xxxx xxxx</li>
      <li>P:(555) 555-5555</li>
      <li>F:(555) 555-5555</li>
      <li>peter@voltinapartners.com.au</li>
    </ul>
    <span class="edge-stripe"></span>
  </section>

  <section class="card card--back" aria-label="Business card back">
    <div class="brand"><span class="brand__mark"></span>Voltina Partners</div>
    <p class="website">www.voltinapartners.com.au</p>
    <span class="edge-shade"></span>
  </section>
</main>
</body>
</html>
```